Business Card, A4 Letter Head and DL Envelope for Brandvelle

We are looking for a design for our Business Card, A4 Letter Head and DL Envelope.

Brandvelle is a distributor of promotional products. We specialize in a range of branded promotional products, these include pens, polo shirts, key rings, drink bottles, uniforms and bags to name a few. We are experts in marketing and assist companies in choosing the right promotional product for their needs. We will predominately be an online business where customers visit our website and browse our range of promotional products and branding options.

Our colours are black, red, white and grey.

Files must be supplied in eps, pdf and ai format.

Please display the following information:
Derek Halloway
Account Manager
Suite xxx, 212 Ferrow Lane Melbourne, Victoria 3000
Phone +61 3 5550 1827
Mobile +61 455 016 342
sales@brandvelle-example.com.au
www.brandvelle-example.com.au

```html
<!DOCTYPE html>
<html lang="en">
<head>
<meta charset="utf-8">
<title>Brandvelle Business Card</title>
<link rel="stylesheet" href="https://fonts.googleapis.com/css2?family=Exo+2:wght@600;700&family=Arimo:wght@400&display=swap">
<style>
  :root {
    --brand-red: #c01c22;
    --paper: #ffffff;
    --ink-grey: #3a3a3c;
    --stage-top: #8a8a8a;
    --stage-bottom: #676767;
  }
  * { margin: 0; padding: 0; box-sizing: border-box; }
  html, body { width: 1200px; height: 1000px; overflow: hidden; }
  body {
    background: linear-gradient(180deg, var(--stage-top), var(--stage-bottom));
    font-family: "Arimo", Arial, sans-serif;
  }
  .card {
    position: absolute;
    top: 343px;
    width: 525px;
    height: 313px;
    background: var(--paper);
    box-shadow: 0 3px 8px rgba(0,0,0,0.45);
    overflow: hidden;
  }
  .card--front { left: 47px; }
  .card--back { left: 635px; }

  /* Front */
  .front__panel {
    position: absolute; left: 0; top: 0;
    width: 100%; height: 229px;
    background: var(--brand-red);
    color: var(--paper);
  }
  .holder {
    position: absolute; left: 270px; top: 18px;
  }
  .holder__name {
    font-family: "Exo 2", Arial, sans-serif;
    font-weight: 700;
    font-size: 25px;
    letter-spacing: 0.3px;
    line-height: 1.1;
  }
  .holder__role { font-size: 15px; margin-top: 2px; }
  .contact {
    position: absolute; left: 42px; top: 119px;
    list-style: none;
    font-size: 14px;
    line-height: 19.5px;
  }
  .contact__label { display: inline-block; width: 20px; font-size: 13px; }
  .address {
    position: absolute; left: 41px; top: 181px;
    font-size: 14.5px; line-height: 18px;
  }
  .front__brand {
    position: absolute; left: 0; top: 229px;
    width: 100%; height: 84px;
    display: flex; align-items: center; justify-content: center; gap: 10px;
  }

  /* Brand lockup */
  .brand-dot {
    display: block;
    border-radius: 50%;
    background: var(--brand-red);
  }
  .brand-name {
    font-family: "Exo 2", Arial, sans-serif;
    font-weight: 700;
    color: var(--ink-grey);
    letter-spacing: 0.5px;
  }
  .front__brand .brand-dot { width: 34px; height: 34px; }
  .front__brand .brand-name { font-size: 22px; }

  /* Back */
  .back__brand {
    position: absolute; left: 0; top: 40px;
    width: 100%;
    display: flex; flex-direction: column; align-items: center; gap: 22px;
  }
  .back__brand .brand-dot { width: 86px; height: 86px; }
  .back__brand .brand-name { font-size: 29px; }
  .web-band {
    position: absolute; left: 0; top: 202px;
    width: 100%; height: 26px;
    background: var(--brand-red);
    color: var(--paper);
    font-size: 14.5px;
    text-align: center;
    line-height: 26px;
  }
</style>
</head>
<body>
  <section class="card card--front" aria-label="Business card front">
    <div class="front__panel">
      <div class="holder">
        <p class="holder__name">Derek Halloway</p>
        <p class="holder__role">Account Manager</p>
      </div>
      <ul class="contact">
        <li><span class="contact__label">M</span>+61 455 016 342</li>
        <li><span class="contact__label">T</span>+61 3 5550 1827</li>
        <li><span class="contact__label">E</span>sales@brandvelle-example.com.au</li>
      </ul>
      <p class="address">Suite xxx, 212 Ferrow Lane<br>Melbourne, Victoria 3000</p>
    </div>
    <div class="front__brand">
      <span class="brand-dot" aria-hidden="true"></span>
      <span class="brand-name">BRANDVELLE</span>
    </div>
  </section>

  <section class="card card--back" aria-label="Business card back">
    <div class="back__brand">
      <span class="brand-dot" aria-hidden="true"></span>
      <span class="brand-name">BRANDVELLE</span>
    </div>
    <div class="web-band">www.brandvelle-example.com.au</div>
  </section>
</body>
</html>
```